Small Business Broker Business Card Design

A business card design for a small business brokerage, which is a financial service, not unlike real estate brokerage, but for small businesses such as laundromats, pizza shops, restaurants, cleaners etc. The designs should all be simple, more conservative in nature, using the colors and font of the logo. Again, think real estate Brokerage as a business context
Contact Information for Business Card
Name: Glen R. Harlow. Title: Small Business Advisor. Email: g.harlow@bayfieldcapitalworks.example. Mobile: (555) 274-3918. Office: (555) 806-2147. www.bayfieldcapitalworks.example

```html
<!DOCTYPE html>
<html lang="en">
<head>
<meta charset="utf-8">
<title>Bayfield Capital Works – Business Card</title>
<link href="https://fonts.googleapis.com/css2?family=Josefin+Sans:wght@600;700&family=Montserrat:wght@400;500&display=swap" rel="stylesheet">
<style>
  :root {
    --navy: #1a3668;
    --navy-soft: #1e3d6f;
    --green: #8bc440;
    --paper: #f3f3f2;
    --ink: #2b2b2b;
    --backdrop: #1c1c1c;
  }
  * { box-sizing: border-box; margin: 0; padding: 0; }
  html, body { width: 1200px; height: 1059px; overflow: hidden; background: var(--backdrop); }
  .canvas { position: relative; width: 1200px; height: 1059px; }

  .card { position: absolute; overflow: hidden; }
  .card--front { left: 256px; top: 89px; width: 688px; height: 391px; background: var(--paper); }
  .card--back { left: 253px; top: 546px; width: 695px; height: 394px; background: var(--navy-soft); }

  .brand { position: absolute; left: 0; right: 0; text-align: center; }
  .brand__name {
    display: inline-flex; align-items: center; gap: 10px;
    font-family: "Josefin Sans", sans-serif; font-weight: 700; letter-spacing: 0.3px;
  }
  .brand__mark { display: inline-block; background: var(--green); }
  .brand__tagline {
    font-family: "Montserrat", sans-serif; font-weight: 500; color: var(--green);
    text-transform: uppercase;
  }

  .card--front .brand { top: 126px; }
  .card--front .brand__name { font-size: 21px; color: var(--navy); }
  .card--front .brand__mark { width: 16px; height: 16px; }
  .card--front .brand__tagline { font-size: 9.5px; letter-spacing: 1.6px; margin-top: 4px; }

  .person { position: absolute; right: 366px; top: 227px; text-align: right; }
  .person__name {
    font-family: "Josefin Sans", sans-serif; font-weight: 700; font-size: 28px;
    color: var(--navy); white-space: nowrap; letter-spacing: 0.3px;
  }
  .person__name .surname { color: var(--green); }
  .person__title { font-family: "Montserrat", sans-serif; font-size: 15px; color: var(--ink); margin-top: 2px; }

  .divider { position: absolute; left: 343px; top: 214px; width: 1.5px; height: 89px; background: var(--navy); }

  .contacts { position: absolute; left: 366px; top: 206px; list-style: none; }
  .contacts li {
    display: flex; align-items: center; height: 26px;
    font-family: "Montserrat", sans-serif; font-size: 14px; color: var(--ink); white-space: nowrap;
  }
  .contacts svg { width: 13px; height: 13px; margin-right: 10px; fill: var(--green); flex: none; }

  .address {
    position: absolute; left: 0; right: 0; top: 336px; text-align: center;
    font-family: "Montserrat", sans-serif; font-size: 15px; color: var(--ink); letter-spacing: 0.2px;
  }
  .band { position: absolute; left: 0; bottom: 0; width: 688px; height: 14px; }

  .card--back .brand { top: 248px; }
  .card--back .brand__name { font-size: 30px; color: #ffffff; }
  .card--back .brand__mark { width: 22px; height: 22px; }
  .card--back .brand__tagline { font-size: 14px; letter-spacing: 2px; margin-top: 4px; }
</style>
</head>
<body>
<main class="canvas">

  <section class="card card--front">
    <div class="brand">
      <div class="brand__name"><span class="brand__mark"></span>BAYFIELD CAPITAL WORKS, INC</div>
      <div class="brand__tagline">Trusted guidance to buy or sell a local business</div>
    </div>

    <div class="person">
      <div class="person__name">GLEN R. <span class="surname">HARLOW</span></div>
      <div class="person__title">Small Business Advisor</div>
    </div>

    <div class="divider"></div>

    <ul class="contacts">
      <li>
        <svg viewBox="0 0 16 16" aria-hidden="true"><path d="M1 6c0-2 3-3.5 7-3.5S15 4 15 6v1h-3.5V5.5h-7V7H1z"/><path d="M4 8h8l2 6H2z"/></svg>
        (555) 806-2147
      </li>
      <li>
        <svg viewBox="0 0 16 16" aria-hidden="true"><path d="M4.5 0h7a1 1 0 0 1 1 1v14a1 1 0 0 1-1 1h-7a1 1 0 0 1-1-1V1a1 1 0 0 1 1-1zm.8 2v10h5.4V2zM8 13a1 1 0 1 0 0 2 1 1 0 0 0 0-2z"/></svg>
        (555) 274-3918
      </li>
      <li>
        <svg viewBox="0 0 16 16" aria-hidden="true"><path d="M8 1l7 5v9H1V6zm0 2L3 6.5 8 10l5-3.5z"/></svg>
        g.harlow@bayfieldcapitalworks.example
      </li>
      <li>
        <svg viewBox="0 0 16 16" aria-hidden="true"><path d="M8 0a8 8 0 1 0 0 16A8 8 0 0 0 8 0zM4 3l3 1 1 3-2 1-1 3-2-2V5zm6 1h3l1 3-2 2-2-1z"/></svg>
        www.bayfieldcapitalworks.example
      </li>
    </ul>

    <p class="address">P.O. Box&nbsp; Street Name Country Name AB, A5B 521</p>

    <svg class="band" viewBox="0 0 688 14" preserveAspectRatio="none" aria-hidden="true">
      <polygon points="0,0 352,0 329,14 0,14" fill="var(--navy)"/>
      <polygon points="358,0 688,0 688,14 338,14" fill="var(--green)"/>
    </svg>
  </section>

  <section class="card card--back">
    <div class="brand">
      <div class="brand__name"><span class="brand__mark"></span>BAYFIELD CAPITAL WORKS, INC</div>
      <div class="brand__tagline">Trusted guidance to buy or sell a local business</div>
    </div>
  </section>

</main>
</body>
</html>
```